Wordpress Design Project for Employee Communications Site

We need a Wordpress design for a company that strategizes on and produces materials for employee communications. Improving employee communications at all levels of an organization can help improve overall company performance and results. The site needs to look very clean and professional; we're not afraid of white space. We like the functionality that Wordpress provides; however, we only want one "true" blog page; the other pages should give the impression of a more "static" web site - particularly the home page. I have a logo that I can provide.

I have added these comments to the discussion page:
Great question - thank you for asking it. I’ve done more research

I like the very clean and monochromatic looks to many of these. I don’t have to have monochromatic, but I do like minimal colors. Simple, clean, organized. The home page should “fit” almost entirely without scrolling. I do like fat footers that you can scroll down to. I don’t want a colored background, but any that I’ve chosen with colored backgrounds could be switched to a white background.

http://www.mirabelquennet.example/
http://pondraft.example/
http://v1.samplumworth.example/
http://howdythegoat.example/
http://stayingbrisk.example/
http://www.interiors.kelmun.example/
http://trelvmasters.example/

These last two are more corporate sites. The first one is from a well-respected consultant in my area who does a lot of what I do. And I think Harwenby does a nice job with their site. So, I want to marry the look I like with getting the content job done.

http://www.messagefuelbox.example/
http://www.harwenby.example/view/en_US/us/index.htm

Target Market(s)

Target market is mid- to large-sized companies. More than 500 employees.

Industry/Entity Type

Communications

Requirements
Must have
• Need an impactful home page. There should be a "blog" page; contact us; services; about. For starters, at least. I want fonts to be very readable - that is, either quite dark gray or black.
Nice to have
• I am loathe to include a picture of myself, but I do want some images that say, "professional" and "expert" in communications.
Should not have
• I don't want a hits counter :) (I know no one would do that!).

```html
<!DOCTYPE html>
<html lang="en">
<head>
<meta charset="utf-8">
<title>Corvane Staff Messaging Co.</title>
<link rel="stylesheet" href="https://fonts.googleapis.com/css2?family=Source+Sans+3:wght@300;400;600&display=swap">
<style>
  :root {
    --ink: #333333;
    --ink-soft: #444444;
    --brand-blue: #1f8ac2;
    --nav-active: #2aa3dc;
    --brand-green: #8db21a;
    --brand-purple: #4a3f7a;
    --rule: #707070;
    --divider: #dcdcdc;
    --footer-bg: #f4f4f4;
    --footer-line: #d6d6d6;
    --white: #ffffff;
  }
  * { box-sizing: border-box; margin: 0; padding: 0; }
  html, body { width: 1200px; height: 873px; overflow: hidden; background: var(--white); }
  body { position: relative; font-family: Arial, Helvetica, sans-serif; color: var(--ink); }

  .brand { position: absolute; left: 84px; top: 40px; display: flex; align-items: center; gap: 14px; }
  .brand-dot { width: 38px; height: 38px; border-radius: 50%; background: var(--brand-blue); }
  .brand-name { font-family: "Source Sans 3", sans-serif; font-weight: 400; font-size: 34px; color: var(--brand-purple); letter-spacing: 0.5px; }

  .nav-rule { position: absolute; top: 128px; height: 3px; background: var(--rule); }
  .nav-rule.left { left: 0; width: 667px; }
  .nav-rule.right { left: 1042px; width: 158px; }
  .main-nav { position: absolute; left: 667px; top: 112px; width: 375px; display: flex; align-items: center; font-family: "Source Sans 3", sans-serif; font-weight: 300; font-size: 20px; }
  .main-nav a { position: relative; color: var(--ink); text-decoration: none; padding: 0 14px; line-height: 24px; }
  .main-nav a + a { border-left: 1.5px solid var(--ink); }
  .main-nav a.is-active { color: var(--nav-active); padding-left: 9px; }
  .main-nav a.is-active svg { position: absolute; left: 50%; margin-left: -9px; top: 26px; }

  .hero { position: absolute; left: 91px; top: 154px; width: 981px; height: 263px; background: linear-gradient(180deg, #c9d9e8 0%, #e4ebf1 55%, #d9c3ad 100%); }
  .hero-message { position: absolute; left: 27px; top: 41px; width: 481px; height: 173px; background: rgba(255,255,255,0.78); border: 2px solid rgba(255,255,255,0.95); padding: 11px 18px; font-family: "Source Sans 3", sans-serif; font-size: 27px; line-height: 35px; color: var(--ink-soft); }
  .hero-message strong { color: var(--brand-blue); font-weight: 600; }

  .features { position: absolute; left: 136px; top: 454px; width: 942px; height: 159px; }
  .features .v-line { position: absolute; top: 0; bottom: 0; border-left: 1px dotted var(--divider); }
  .features .h-line { position: absolute; left: 0; right: 0; top: 77px; border-top: 1px dotted var(--divider); }
  .feature { position: absolute; width: 280px; }
  .feature svg { position: absolute; left: 0; top: 4px; }
  .feature h3 { margin-left: 42px; font-family: "Source Sans 3", sans-serif; font-weight: 600; font-size: 17px; line-height: 20px; color: var(--brand-green); }
  .feature p { margin-left: 42px; font-size: 12.5px; line-height: 15.5px; color: var(--ink); }

  .site-footer { position: absolute; left: 0; top: 648px; width: 1200px; height: 190px; background: var(--footer-bg); border-top: 1px solid var(--footer-line); border-bottom: 1px solid var(--footer-line); }
  .footer-col { position: absolute; top: 20px; }
  .footer-col h4 { font-family: "Source Sans 3", sans-serif; font-weight: 600; font-size: 15.5px; color: var(--ink); margin-bottom: 9px; }
  .footer-col li { list-style: none; font-size: 11.5px; line-height: 19.6px; letter-spacing: 0.4px; color: var(--ink); }
  .footer-sep { position: absolute; top: 17px; height: 134px; border-left: 1px solid var(--footer-line); }
  .social { display: flex; gap: 6px; margin-top: 2px; }
  .social span { width: 18px; height: 18px; }

  .copyright { position: absolute; left: 0; top: 847px; width: 1200px; text-align: center; font-size: 11.5px; color: var(--ink); letter-spacing: 0.3px; }
</style>
</head>
<body>
  <header>
    <div class="brand"><span class="brand-dot"></span><span class="brand-name">Corvane Staff Messaging Co.</span></div>
    <div class="nav-rule left"></div>
    <nav class="main-nav">
      <a href="#" class="is-active">works
        <svg width="18" height="8" viewBox="0 0 18 8"><path d="M5 1 L9 5 L13 1" fill="none" stroke="#2aa3dc" stroke-width="1.6"/></svg>
      </a>
      <a href="#">process</a>
      <a href="#">about</a>
      <a href="#">contact</a>
    </nav>
    <div class="nav-rule right"></div>
  </header>

  <section class="hero" role="img" aria-label="Photograph of several hands joining fingers together against a pale sky">
    <div class="hero-message">Now more than ever it is critical to show the value of <strong>Employee Communication</strong> and Engagement to the business.</div>
  </section>

  <section class="features">
    <div class="v-line" style="left:299px"></div>
    <div class="v-line" style="left:631px"></div>
    <div class="h-line"></div>

    <div class="feature" style="left:-2px; top:3px">
      <svg width="34" height="34" viewBox="0 0 34 34"><path d="M7 14 A11 11 0 0 1 27 14" fill="none" stroke="#9ab6c8" stroke-width="2"/><path d="M11 15 A7 7 0 0 1 23 15" fill="none" stroke="#6a9cbf" stroke-width="2"/><circle cx="17" cy="16" r="3" fill="#2a7fbf"/><path d="M17 18 L11 32 L23 32 Z" fill="#4a4a4a"/></svg>
      <h3>Employee Packet</h3>
      <p>Publish messages on desktop backgrounds. Change and sequence messages easily.</p>
    </div>
    <div class="feature" style="left:322px; top:3px">
      <svg width="38" height="38" viewBox="0 0 38 38"><circle cx="22" cy="15" r="12" fill="#2e8fd6" stroke="#1a5d96" stroke-width="2"/><circle cx="19" cy="12" r="4" fill="#9fd2f5"/><path d="M13 24 L4 33" stroke="#555" stroke-width="5" stroke-linecap="round"/></svg>
      <h3>Employee Packet</h3>
      <p>Publish messages on desktop backgrounds. Change and sequence messages easily.</p>
    </div>
    <div class="feature" style="left:671px; top:3px">
      <svg width="34" height="36" viewBox="0 0 34 36"><path d="M12 12 V8 A5 5 0 0 1 22 8 V12" fill="none" stroke="#c77c00" stroke-width="2"/><rect x="6" y="11" width="22" height="23" rx="3" fill="#f7a51c"/></svg>
      <h3>Employee Packet</h3>
      <p>Publish messages on desktop backgrounds. Change and sequence messages easily.</p>
    </div>

    <div class="feature" style="left:-2px; top:91px">
      <svg width="36" height="34" viewBox="0 0 36 34"><circle cx="12" cy="10" r="5" fill="#f0b88a"/><path d="M3 28 A9 9 0 0 1 21 28 Z" fill="#2f86d0"/><circle cx="24" cy="11" r="5" fill="#e8a878"/><path d="M15 29 A9 9 0 0 1 33 29 Z" fill="#6cbf3a"/></svg>
      <h3>Employee Packet</h3>
      <p>Publish messages on desktop backgrounds. Change and sequence messages easily.</p>
    </div>
    <div class="feature" style="left:320px; top:91px">
      <svg width="38" height="38" viewBox="0 0 38 38"><path d="M8 12 V30 H18 M8 20 H18" fill="none" stroke="#888" stroke-width="1.5"/><rect x="2" y="6" width="12" height="8" rx="1" fill="#f3c02a"/><rect x="17" y="16" width="12" height="8" rx="1" fill="#f3c02a"/><rect x="17" y="26" width="12" height="8" rx="1" fill="#f3c02a"/><rect x="24" y="3" width="12" height="8" rx="1" fill="#f3c02a"/></svg>
      <h3>Employee Packet</h3>
      <p>Publish messages on desktop backgrounds. Change and sequence messages easily.</p>
    </div>
    <div class="feature" style="left:670px; top:90px">
      <svg width="38" height="38" viewBox="0 0 38 38"><rect x="8" y="4" width="26" height="8" rx="3" fill="#9a9a9a"/><rect x="8" y="14" width="26" height="8" rx="3" fill="#8a8a8a"/><rect x="8" y="24" width="26" height="8" rx="3" fill="#7a7a7a"/><circle cx="11" cy="24" r="8" fill="#8fc53a" stroke="#5f8f1e" stroke-width="1.5"/><path d="M11 19 V29 M6 24 H16" stroke="#fff" stroke-width="2.4"/></svg>
      <h3>Employee Packet</h3>
      <p>Publish messages on desktop backgrounds. Change and sequence messages easily.</p>
    </div>
  </section>

  <footer class="site-footer">
    <div class="footer-col" style="left:155px"><h4>Company</h4><ul><li>About Us</li><li>Sitemap</li><li>Website Terms</li><li>Terms of Business</li><li>Privacy Policy</li></ul></div>
    <div class="footer-sep" style="left:285px"></div>
    <div class="footer-col" style="left:321px"><h4>Product</h4><ul><li>Business Websites</li><li>Reviews</li><li>Quick Tour</li><li>Pricing</li><li>Free Trial</li></ul></div>
    <div class="footer-sep" style="left:471px"></div>
    <div class="footer-col" style="left:514px"><h4>Internet Marketing</h4><ul><li>Marketing Tips</li><li>Search Optimisation</li><li>Social Media</li><li>Video Marketing</li><li>Business Cases</li></ul></div>
    <div class="footer-sep" style="left:694px"></div>
    <div class="footer-col" style="left:737px"><h4>Services</h4><ul><li>Help/Contact us</li><li>Business directory</li><li>Legal notices</li><li>Privacy policy</li><li>Terms &amp; Conditions</li></ul></div>
    <div class="footer-sep" style="left:887px"></div>
    <div class="footer-col" style="left:923px"><h4>Follow us</h4>
      <div class="social">
        <span style="background:#2a76b0" aria-label="Social network link"></span>
        <span style="background:#3b5a98" aria-label="Social network link"></span>
        <span style="background:#c9c9c9" aria-label="Video channel link"></span>
        <span style="background:#3fa9dd" aria-label="Social network link"></span>
      </div>
    </div>
  </footer>

  <p class="copyright">Copyright © 2012 Corvane Staff Messaging Co. All rights reserved.</p>
</body>
</html>
```